Need Help having my business card stand out

I am the owner of Birchway Canine Training and would like for my business cards to stand out. I have been trying to keep designing them myself but I can't get what I have in my head on the card. I will try my best to post templates that I like for inspirations. I want something unique but elegant. I don't want in to look cartoony or cheesy. It needs to pop in a pet shop but also in a coffee shop or gym.

Target Market(s)

Dog owners, Married ,No young kids Jr High school kids and up (maybe kids on the way) Executives, Stay at home moms/wives, Small business owners

Industry/Entity Type

Dog Training

Contact Information for Business Card

Lowell Spratt, 281-904-3376, info@birchwaycanine.example, www.birchwaycanine.example

Colors

Designer to choose colors to be used in the design.

Requirements
Must have
• my logo
Should not have
• Cursive lettering

```html
<!DOCTYPE html>
<html lang="en">
<head>
<meta charset="utf-8">
<title>Birchway Canine Training – Business Card</title>
<link rel="stylesheet" href="https://fonts.googleapis.com/css2?family=Lato:wght@400;700&display=swap">
<style>
  :root {
    --stage: #c4c4c6;
    --card-black: #0c0c0c;
    --card-black-hi: #262626;
    --card-white: #f4f4f4;
    --ink-light: #f2f2f2;
    --ink-dark: #1c1c1c;
    --icon-grey: #5a5a5a;
    --rule-grey: #8a8a8a;
    --arc-grey: #6e6e6e;
    --photo-a: #b7b09c;
    --photo-b: #8c3a3a;
    --photo-c: #2b3550;
  }
  * { box-sizing: border-box; margin: 0; padding: 0; }
  html, body { width: 1200px; height: 1200px; overflow: hidden; }
  body { background: var(--stage); font-family: "Lato", sans-serif; position: relative; }

  .card { position: absolute; left: 250px; width: 700px; height: 400px; overflow: hidden;
          box-shadow: 0 10px 18px rgba(0,0,0,.25); }
  .card--front { top: 150px; background: linear-gradient(160deg, var(--card-black-hi) 0%, var(--card-black) 45%, var(--card-black) 100%); }
  .card--back { top: 630px; background: var(--card-white); }

  .card__photo-layer { position: absolute; inset: 0; }

  .brand-name { position: absolute; color: var(--ink-light); font-weight: 700;
                font-size: 26px; line-height: 1.1; text-align: center; width: 220px; }
  .card--front .brand-name { left: 22px; top: 72px; }
  .card--back .brand-name { color: var(--ink-dark); left: 0; top: 226px; width: 220px; }

  .contact { position: absolute; left: 38px; color: var(--ink-light); font-size: 18px;
             display: flex; align-items: center; gap: 10px; }
  .contact svg { width: 16px; height: 16px; flex: none; }
  .contact--phone { top: 188px; }
  .contact--email { top: 240px; }
  .contact--web { top: 268px; }

  .holder { position: absolute; top: 324px; left: 0; width: 400px; display: flex; align-items: center; }
  .holder__rule { height: 1px; background: var(--rule-grey); flex: 1; }
  .holder__name { color: var(--ink-light); font-weight: 700; font-size: 20px; padding: 0 14px; letter-spacing: .2px; }

  .back-url { position: absolute; left: 46px; top: 330px; font-size: 18px; color: var(--ink-dark); }
</style>
</head>
<body>

<section class="card card--front">
  <svg class="card__photo-layer" width="700" height="400" viewBox="0 0 700 400">
    <defs>
      <linearGradient id="photoTone" x1="0" y1="0" x2="1" y2="1">
        <stop offset="0" stop-color="var(--photo-a)"/>
        <stop offset=".5" stop-color="var(--photo-b)"/>
        <stop offset="1" stop-color="var(--photo-c)"/>
      </linearGradient>
    </defs>
    <path d="M418 0 Q340 200 460 400 L700 400 L700 0 Z" fill="var(--arc-grey)"/>
    <path role="img" aria-label="Photo of the trainer kneeling beside a shepherd dog outdoors"
          d="M432 0 Q356 200 474 400 L700 400 L700 0 Z" fill="url(#photoTone)"/>
  </svg>

  <div class="brand-name">Birchway Canine Training</div>

  <div class="contact contact--phone">
    <svg viewBox="0 0 16 16"><rect width="16" height="16" rx="2" fill="var(--icon-grey)"/><path d="M5 3.5l2 2-1 1.2c.6 1.3 1.6 2.3 2.9 2.9l1.2-1 2 2-1.2 1.6C7.6 12 4 8.4 3.8 4.8z" fill="#1a1a1a"/></svg>
    <span>281-904-3376</span>
  </div>
  <div class="contact contact--email">
    <svg viewBox="0 0 16 16"><rect width="16" height="16" rx="2" fill="var(--icon-grey)"/><rect x="3.5" y="5" width="9" height="6" fill="none" stroke="#1a1a1a" stroke-width="1"/><path d="M3.5 5L8 8.5 12.5 5" fill="none" stroke="#1a1a1a" stroke-width="1"/></svg>
    <span>info@birchwaycanine.example</span>
  </div>
  <div class="contact contact--web">
    <svg viewBox="0 0 16 16"><rect width="16" height="16" rx="2" fill="var(--icon-grey)"/><circle cx="8" cy="8" r="4.5" fill="none" stroke="#1a1a1a" stroke-width="1"/><path d="M3.5 8h9M8 3.5c-2 2.5-2 6.5 0 9M8 3.5c2 2.5 2 6.5 0 9" fill="none" stroke="#1a1a1a" stroke-width="1"/></svg>
    <span>www.birchwaycanine.example</span>
  </div>

  <div class="holder">
    <span class="holder__rule"></span>
    <span class="holder__name">LOWELL SPRATT</span>
    <span class="holder__rule"></span>
  </div>
</section>

<section class="card card--back">
  <div class="brand-name">Birchway Canine Training</div>
  <div class="back-url">www.birchwaycanine.example</div>
</section>

</body>
</html>
```